Online homewares store needs a web design

We need a web design for a new high-end online homewares store. We are starting small with only 5 major categories.

Rugs
Bathe
Dine
Decorative
Sleep

This is just for design. No coding needed.

Please make high-end, sophisticated and minimal.

I have included some pictures to give you an idea of the products. I would like to showcase some of the pictures on the web page.

The website will be using an e-commerce function.

I have included the logo studio nine harbors.

I like this website
http://mapleandquarrylane.example/

or

borvanest.example.au

Simple but effective - not too busy

Project Deadline Extended
Reason: I would like to extend my deadline to give designers more time to do quality work - as requested!! Thanks.

Target Market(s)

Females in the age bracket of 25-45

Males who are very house proud 25-45

Industry/Entity Type

Store

Requirements
Must have
• Upmarket

```html
<!DOCTYPE html>
<html lang="en">
<head>
<meta charset="utf-8">
<title>studio nine harbors — Homewares</title>
<link href="https://fonts.googleapis.com/css2?family=Nunito+Sans:wght@300;400;600;700&display=swap" rel="stylesheet">
<style>
  :root {
    --ink: #000000;
    --white: #ffffff;
    --accent: #ec3a7c;
    --accent-veil: rgba(236, 58, 124, 0.86);
    --charcoal: #2b2b2b;
    --grey-text: #555555;
    --grey-light: #7a7a7a;
    --rule: #cfcfcf;
    --icon: #4a4a4a;
    --caption-bar: rgba(40, 36, 36, 0.62);
  }
  * { box-sizing: border-box; margin: 0; padding: 0; }
  html, body { width: 1077px; height: 1200px; overflow: hidden; }
  body { position: relative; background: var(--white); font-family: "Nunito Sans", Arial, sans-serif; }

  .site-header { position: absolute; left: 0; top: 0; width: 1077px; height: 164px; background: var(--ink); color: var(--white); }
  .brand { position: absolute; left: 73px; top: 72px; font-size: 48px; font-weight: 300; letter-spacing: -0.5px; color: var(--white); line-height: 1; }
  .account-links { position: absolute; right: 254px; top: 37px; font-size: 13px; color: var(--white); }
  .account-links span { margin: 0 6px; }
  .cart { position: absolute; right: 77px; top: 36px; font-size: 13.5px; display: flex; align-items: center; gap: 7px; }
  .main-nav { position: absolute; right: 77px; top: 94px; display: flex; gap: 0; }
  .main-nav a { display: block; height: 33px; line-height: 33px; padding: 0 15px; margin-left: 6px; font-size: 14.5px; color: var(--white); text-decoration: none; }
  .main-nav a.current { background: var(--accent); }
  .main-nav a:last-child { padding-right: 0; }

  .hero { position: absolute; left: 0; top: 164px; width: 1077px; height: 795px;
    background: linear-gradient(100deg, #c9b9a4 0%, #e6ddd0 25%, #f3efe8 45%, #d9d0c3 60%, #bfc9b8 80%, #9db58c 100%); }
  .hero-copy { position: absolute; left: 215px; top: 205px; color: var(--white); }
  .hero-title { font-size: 40px; font-weight: 700; letter-spacing: 0.5px; line-height: 1; }
  .hero-subtitle { margin-top: 17px; font-size: 19.5px; font-weight: 600; letter-spacing: 0.4px; }
  .hero-text { margin-top: 12px; font-size: 15px; line-height: 23px; width: 380px; }
  .slide-arrow { position: absolute; top: 220px; width: 55px; height: 55px; border-radius: 50%; background: rgba(60, 60, 60, 0.55); }
  .slide-arrow.prev { left: 77px; }
  .slide-arrow.next { left: 943px; }
  .slide-arrow svg { position: absolute; left: 19px; top: 16px; }

  .products-band { position: absolute; left: 0; top: 646px; width: 1077px; height: 313px; background: var(--accent-veil); }
  .products-heading { position: absolute; left: 0; width: 100%; top: 42px; display: flex; justify-content: center; align-items: center; gap: 14px; color: var(--white); font-size: 21.5px; font-weight: 400; }
  .product-card { position: absolute; top: 99px; width: 284px; height: 167px; }
  .product-card .photo { position: absolute; inset: 0; }
  .product-card .caption { position: absolute; left: 0; bottom: 0; width: 100%; height: 43px; background: var(--caption-bar); color: var(--white); font-size: 17px; padding-left: 17px; line-height: 43px; }
  .product-card .caption svg { position: absolute; right: 12px; top: 10px; }
  .card-rugs { left: 78px; } .card-rugs .photo { background: linear-gradient(135deg, #d8406a, #e3a94a 35%, #5aa1c9 65%, #c9a58c); }
  .card-decorative { left: 395px; } .card-decorative .photo { background: linear-gradient(160deg, #b08a47, #6d5532 55%, #d9d4cc); }
  .card-bathe { left: 715px; } .card-bathe .photo { background: linear-gradient(120deg, #cfd3d6, #eef0f1 45%, #9aa0a3); }

  .contact-bar { position: absolute; left: 0; top: 959px; width: 1077px; height: 115px; background: var(--white); font-family: Arial, Helvetica, sans-serif; }
  .contact-item { position: absolute; display: flex; align-items: center; }
  .contact-address { left: 80px; top: 40px; }
  .contact-address .lines { margin-left: 20px; }
  .contact-address .line-main { font-size: 14.5px; color: var(--grey-text); }
  .contact-address .line-sub { font-size: 12px; color: var(--grey-light); margin-top: 6px; }
  .contact-phone { left: 480px; top: 47px; font-size: 14px; color: var(--grey-text); gap: 14px; }
  .contact-mail { right: 78px; top: 49px; font-size: 14.5px; color: var(--grey-text); gap: 14px; }
  .divider { position: absolute; top: 43px; width: 1px; height: 39px; background: var(--rule); }

  .site-footer { position: absolute; left: 0; top: 1074px; width: 1077px; height: 126px; background: var(--charcoal); color: var(--white); font-family: Arial, Helvetica, sans-serif; }
  .footer-nav { position: absolute; left: 74px; top: 42px; font-size: 12.5px; }
  .footer-nav span { margin: 0 6px; }
  .copyright { position: absolute; left: 74px; top: 75px; font-size: 12.5px; }
  .social { position: absolute; left: 789px; top: 42px; display: flex; gap: 14px; }
  .social span { width: 42px; height: 42px; border: 1.5px solid #bdbdbd; border-radius: 50%; }
</style>
</head>
<body>
  <header class="site-header">
    <div class="brand">studio nine harbors</div>
    <div class="account-links">Register<span>|</span>Login<span>|</span>My Account</div>
    <div class="cart">
      <svg width="17" height="15" viewBox="0 0 17 15" aria-hidden="true"><path d="M1 2h3l2 8h8l2-6H5" fill="none" stroke="#fff" stroke-width="1.4"/><circle cx="7" cy="13" r="1.3" fill="#fff"/><circle cx="13" cy="13" r="1.3" fill="#fff"/></svg>
      Cart (0) items
    </div>
    <nav class="main-nav">
      <a class="current">HOME</a><a>ABOUT US</a><a>PRODUCTS</a><a>CONTACT US</a>
    </nav>
  </header>

  <section class="hero" role="img" aria-label="Bright modern open-plan kitchen with white island, bar stools and dining area by garden doors">
    <div class="slide-arrow prev"><svg width="14" height="22" viewBox="0 0 14 22"><path d="M11 2 3 11l8 9" fill="none" stroke="#fff" stroke-width="1.6"/></svg></div>
    <div class="slide-arrow next"><svg width="14" height="22" viewBox="0 0 14 22"><path d="M3 2l8 9-8 9" fill="none" stroke="#fff" stroke-width="1.6"/></svg></div>
    <div class="hero-copy">
      <h1 class="hero-title">DUIS AUTEM VEL EUM</h1>
      <h2 class="hero-subtitle">ELEIFEND OPTION CON&nbsp; ANTEPOSUERIT</h2>
      <p class="hero-text">Duis autem vel eum iriure dolor in hendrerit in vulputate velit esse molestie consequat el eu feugiat nulla.</p>
    </div>
  </section>

  <section class="products-band">
    <h3 class="products-heading">
      <svg width="17" height="17" viewBox="0 0 17 17" aria-hidden="true"><circle cx="8.5" cy="8.5" r="7.5" fill="none" stroke="rgba(255,255,255,0.7)" stroke-width="1.4"/><path d="M10 5 6.5 8.5 10 12" fill="none" stroke="rgba(255,255,255,0.7)" stroke-width="1.4"/></svg>
      OUR MAJOR PRODUCTS
      <svg width="17" height="17" viewBox="0 0 17 17" aria-hidden="true"><circle cx="8.5" cy="8.5" r="7.5" fill="none" stroke="rgba(255,255,255,0.7)" stroke-width="1.4"/><path d="M7 5l3.5 3.5L7 12" fill="none" stroke="rgba(255,255,255,0.7)" stroke-width="1.4"/></svg>
    </h3>
    <article class="product-card card-rugs">
      <div class="photo" role="img" aria-label="Child's bare feet on a colourful felt-ball rug"></div>
      <div class="caption">RUGS<svg width="24" height="24" viewBox="0 0 24 24"><circle cx="12" cy="12" r="10.5" fill="none" stroke="#fff" stroke-width="1.5"/><path d="M10 7l5 5-5 5" fill="none" stroke="#fff" stroke-width="1.5"/></svg></div>
    </article>
    <article class="product-card card-decorative">
      <div class="photo" role="img" aria-label="Stack of black and white patterned cushions before a gold lattice screen"></div>
      <div class="caption">DECORATIVE<svg width="24" height="24" viewBox="0 0 24 24"><circle cx="12" cy="12" r="10.5" fill="none" stroke="#fff" stroke-width="1.5"/><path d="M10 7l5 5-5 5" fill="none" stroke="#fff" stroke-width="1.5"/></svg></div>
    </article>
    <article class="product-card card-bathe">
      <div class="photo" role="img" aria-label="Bright marble bathroom with glass shower and vanity"></div>
      <div class="caption">BATHE<svg width="24" height="24" viewBox="0 0 24 24"><circle cx="12" cy="12" r="10.5" fill="none" stroke="#fff" stroke-width="1.5"/><path d="M10 7l5 5-5 5" fill="none" stroke="#fff" stroke-width="1.5"/></svg></div>
    </article>
  </section>

  <section class="contact-bar">
    <div class="contact-item contact-address">
      <svg width="24" height="33" viewBox="0 0 24 33" aria-hidden="true"><path d="M12 1C6 1 1.5 5.5 1.5 11.5 1.5 19 12 32 12 32s10.5-13 10.5-20.5C22.5 5.5 18 1 12 1z" fill="var(--icon)"/><circle cx="12" cy="11.5" r="4" fill="#fff"/></svg>
      <div class="lines">
        <div class="line-main">Duis autem vel eum iriureHendrerit.</div>
        <div class="line-sub">Typi non habent claritatem insitam</div>
      </div>
    </div>
    <div class="divider" style="left:405px"></div>
    <div class="contact-item contact-phone">
      <svg width="26" height="28" viewBox="0 0 26 28" aria-hidden="true"><path d="M6 1l4 6-3 3c1.5 4 5 8 9 10l3-3 6 4-2 5c-10 1-22-12-21-22z" fill="var(--icon)"/></svg>
      123 - 456 - 789
    </div>
    <div class="divider" style="left:689px"></div>
    <div class="contact-item contact-mail">
      <svg width="41" height="24" viewBox="0 0 41 24" aria-hidden="true"><rect x="0" y="0" width="41" height="24" fill="var(--icon)"/><path d="M1 1l19.5 13L40 1M1 23l14-11M40 23 26 12" fill="none" stroke="#fff" stroke-width="1.3"/></svg>
      info@ninehaborsmail.example
    </div>
  </section>

  <footer class="site-footer">
    <nav class="footer-nav">Home<span>|</span>About Us<span>|</span>Products<span>|</span>Contact Us</nav>
    <div class="copyright">Copyright © 2013. All Rights Reserved.</div>
    <div class="social" aria-label="Social links"><span></span><span></span><span></span><span></span></div>
  </footer>
</body>
</html>
```